Business Card Design

We are looking for a business card designed for our landscaping company. We do landscaping installation & Maintenance Services. We would like to see designs that have basic landscaping in background. We also think it is important to have both of our names and phone numbers on the card. We need something that stands out a little whether it is shape of the card or thickness or design.

Business

Bramblewood Yardworks, bramblewoodyard@mailvista.net, Owen Platt 555-273-9104, Daniel Korbin 555-618-3927

```html
<!DOCTYPE html>
<html lang="en">
<head>
<meta charset="utf-8">
<title>Bramblewood Yardworks – Business Card</title>
<link href="https://fonts.googleapis.com/css2?family=Arimo:wght@400;700&display=swap" rel="stylesheet">
<style>
  :root {
    --card-bg: #ffffff;
    --ink: #000000;
    --leaf: #9cf01c;
  }
  html, body {
    margin: 0;
    padding: 0;
    width: 1200px;
    height: 700px;
    overflow: hidden;
    background: var(--card-bg);
  }
  .card {
    position: relative;
    width: 1200px;
    height: 700px;
    background: var(--card-bg);
    font-family: "Arimo", Arial, Helvetica, sans-serif;
  }
  .card-frame {
    position: absolute;
    left: 0;
    top: 0;
  }
  .company-name {
    margin: 0;
    font-weight: 400;
  }
  .name-line {
    position: absolute;
    left: 66px;
    font-size: 105px;
    line-height: 1;
    color: var(--ink);
    letter-spacing: 0;
    white-space: nowrap;
  }
  .name-line--accent { color: var(--leaf); }
  .line-1 { top: 55px; }
  .line-2 { top: 164px; }
  .line-3 { top: 283px; }
  .line-4 { top: 400px; }

  .contact {
    position: absolute;
    left: 74px;
    color: var(--leaf);
    white-space: nowrap;
    line-height: 1;
  }
  .contact-email {
    top: 513px;
    font-size: 30px;
  }
  .contact-person {
    font-size: 29px;
  }
  .contact-person .person-name {
    font-weight: 700;
    margin-right: 12px;
  }
  .person-1 { top: 562px; }
  .person-2 { top: 605px; }
</style>
</head>
<body>
  <div class="card">
    <svg class="card-frame" width="1200" height="700" viewBox="0 0 1200 700" aria-hidden="true">
      <rect x="43" y="34" width="1114" height="632" rx="18" ry="18"
            fill="none" stroke="var(--leaf)" stroke-width="3.5"/>
    </svg>

    <h1 class="company-name" aria-label="Bramblewood Yardworks">
      <span class="name-line line-1">BRAMBLE</span>
      <span class="name-line line-2">WOOD</span>
      <span class="name-line name-line--accent line-3">YARD</span>
      <span class="name-line line-4">WORKS</span>
    </h1>

    <div class="contact contact-email">bramblewoodyard@mailvista.net</div>
    <div class="contact contact-person person-1">
      <span class="person-name">Owen Platt</span><span class="person-phone">555 273 9104</span>
    </div>
    <div class="contact contact-person person-2">
      <span class="person-name">Daniel Korbin</span><span class="person-phone">555 618 3927</span>
    </div>
  </div>
</body>
</html>
```